Velmo Swinger site - new website, blogsite and merchandise point, connection to tradeva

We are a well established Swingers Club in the North east of UK and already have an existing site. www.velmo-example.co.uk, BUT we have changed our logo and our information on the site needs to be updated.

We are changing our hosting site to Nimbrashost.example ,also wanting to start a blog which is linked to the club, plus we wish to sell a small exclusive range of Velmo linked merchandise which will also be available on Tradeva.

I have attached a pdf of the majority of the content. additionally we will provide pictures and a videoclip which should be able to be viewed by pc's, lap tops and mobile phones (the whole website must be fully accessible via phone).

The new site must be able to be updated by someone with medium computer knowledge (usually me), by no means expert. Updates will generally be new pictures and written information. The site must be able to be transferred to NimbrasHost.

Velmo is one of the countries leading clubs and emphasises friendliness, fun & safety for its members, we look after you to ensure your experience is the best we can offer. We are very proud of our reputation, built up over more than 10 years.

Target Market(s)

Swingers, dreamers & fantasists, alternative lifestyle people

Coding

Coded - Design and coding required

Number of Pages Required

5+ page

Font styles to use
Sans Serif

Colors
000000
ec1f27
fbfbfb
eeeeee
eaeaea

Requirements
Must have
• website with blog attached, link to tradeva & quidlo, ability to run videoclip and picture album and must be compatable to transfer easily to Nimbrashost and be updated by non-professional (who can learn)
• Straightforward & easy to navigate
• over 18 content page with enter button
Nice to have
• sexy site
• link to chirpster maybe
• black site would be nice with red or white writing
Should not have
• children and animals in anyway shape or form

```html
<!DOCTYPE html>
<html lang="en">
<head>
<meta charset="utf-8">
<title>Velmo – Swingers Club</title>
<link rel="stylesheet" href="https://fonts.googleapis.com/css2?family=Raleway:wght@400;500;600;700;800&display=swap">
<style>
  :root {
    --black: #000000;
    --red: #ec1f27;
    --white: #fbfbfb;
    --light: #eeeeee;
    --grey: #eaeaea;
    --panel: #111111;
    --footer: #0a0a0a;
    --muted: #9a9a9a;
  }
  * { margin: 0; padding: 0; box-sizing: border-box; }
  html, body { width: 1200px; height: 2616px; overflow: hidden; }
  body {
    background: var(--black);
    color: var(--white);
    font-family: "Raleway", sans-serif;
    position: relative;
  }

  /* Header */
  .site-header { position: absolute; left: 0; top: 0; width: 1200px; height: 113px; background: #0b0b0b; }
  .brand { position: absolute; left: 75px; top: 28px; font-size: 44px; font-weight: 500; letter-spacing: 3px; color: var(--white); }
  .main-nav { position: absolute; left: 317px; top: 45px; display: flex; gap: 26px; list-style: none; }
  .main-nav li { font-size: 12.5px; font-weight: 700; text-transform: uppercase; color: var(--white); }
  .main-nav li.active { color: var(--red); }

  /* Hero */
  .hero { position: absolute; left: 75px; top: 113px; width: 1050px; height: 463px; border: 7px solid var(--white); }
  .hero-photo { position: absolute; inset: 0; background: radial-gradient(ellipse at 45% 55%, #b4542a 0%, #6e2612 45%, #2a0b06 100%); }
  .hero-text { position: absolute; left: 0; right: 0; top: 134px; text-align: center; color: var(--white); }
  .hero-title { font-size: 46px; font-weight: 800; letter-spacing: 0.5px; }
  .hero-title span { color: var(--red); }
  .hero-sub { font-size: 29px; font-weight: 700; margin-top: 10px; }
  .hero-lead { font-size: 24px; font-weight: 600; line-height: 31px; margin-top: 6px; }
  .hero-dots { position: absolute; left: 0; right: 0; top: 412px; display: flex; justify-content: center; gap: 8px; }
  .hero-dots i { width: 12px; height: 12px; border-radius: 50%; background: var(--white); display: block; }
  .hero-dots i.on { background: var(--red); }

  /* Intro */
  .intro { position: absolute; left: 75px; top: 620px; width: 1050px; text-align: center; }
  .intro h1 { font-size: 26px; font-weight: 700; line-height: 32px; color: var(--red); }
  .intro h1 b { color: var(--white); }
  .intro p { font-size: 14.5px; line-height: 22px; margin-top: 14px; color: var(--white); }
  .intro p:first-of-type { margin-top: 30px; }
  .intro em { color: var(--red); font-style: normal; font-weight: 700; }
  .btn-more { position: absolute; left: 497px; top: 954px; width: 206px; height: 54px; background: var(--light); color: var(--black); font-size: 17px; font-weight: 700; text-align: center; line-height: 54px; }
  .divider { position: absolute; left: 75px; top: 1064px; width: 1050px; height: 1px; background: #333; }

  /* Info columns */
  .info { position: absolute; top: 1105px; width: 500px; }
  .info.dress { left: 75px; }
  .info.alcohol { left: 623px; }
  .info-head { display: flex; align-items: center; gap: 14px; height: 54px; }
  .info-head h2 { font-size: 26px; font-weight: 700; }
  .info p { font-size: 14.5px; line-height: 22px; margin-top: 12px; }
  .info p:first-of-type { margin-top: 18px; }
  .info em { color: var(--red); font-style: normal; font-weight: 700; }

  /* Blog */
  .blog { position: absolute; left: 0; top: 1456px; width: 1200px; height: 454px; background: var(--panel); }
  .section-title { text-align: center; font-size: 25px; font-weight: 700; text-transform: uppercase; }
  .blog .section-title { margin-top: 53px; }
  .blog-list { position: absolute; left: 75px; top: 110px; display: flex; gap: 30px; }
  .post { width: 330px; }
  .post-photo { width: 330px; height: 188px; }
  .post h3 { font-size: 16px; font-weight: 800; line-height: 26px; text-transform: uppercase; margin-top: 20px; }
  .post time { display: block; font-size: 12px; font-weight: 700; color: var(--red); margin-top: 9px; }

  /* Merchandise */
  .shop { position: absolute; left: 0; top: 1910px; width: 1200px; height: 448px; background: var(--red); }
  .shop .section-title { margin-top: 41px; }
  .products { position: absolute; left: 75px; top: 99px; display: flex; gap: 28px; }
  .product { width: 241px; height: 305px; background: var(--white); text-align: center; position: relative; }
  .product-photo { width: 180px; height: 160px; margin: 14px auto 0; border-radius: 4px; }
  .product h4 { font-size: 14px; font-weight: 700; color: var(--red); text-transform: uppercase; margin-top: 20px; }
  .product p { font-size: 13.5px; color: #555; margin-top: 6px; }
  .product-buy { position: absolute; left: 24px; right: 20px; top: 248px; display: flex; justify-content: space-between; align-items: center; }
  .price { font-size: 17px; font-weight: 700; color: var(--red); }
  .store { font-size: 27px; font-weight: 800; color: var(--black); letter-spacing: -0.5px; }

  /* Footer */
  .site-footer { position: absolute; left: 0; top: 2358px; width: 1200px; height: 258px; background: var(--footer); }
  .footer-brand { position: absolute; left: 75px; top: 95px; font-size: 44px; font-weight: 500; letter-spacing: 3px; }
  .copyright { position: absolute; left: 75px; top: 172px; font-size: 12px; line-height: 22px; color: var(--muted); }
  .footer-col h5 { font-size: 16px; font-weight: 700; text-transform: uppercase; letter-spacing: 0.5px; }
  .sitemap { position: absolute; left: 323px; top: 40px; }
  .sitemap ul { position: absolute; top: 40px; list-style: none; width: 170px; }
  .sitemap ul li { font-size: 13px; line-height: 29px; color: #cfcfcf; }
  .newsletter { position: absolute; left: 623px; top: 40px; width: 230px; }
  .newsletter p { font-size: 13px; line-height: 22px; color: #cfcfcf; margin-top: 14px; }
  .signup { display: flex; margin-top: 17px; height: 38px; }
  .signup span { width: 177px; background: var(--white); color: #666; font-size: 12.5px; line-height: 38px; padding-left: 12px; }
  .signup b { width: 46px; background: var(--red); display: flex; align-items: center; justify-content: center; }
  .follow { position: absolute; left: 905px; top: 40px; }
  .social { display: flex; gap: 16px; margin-top: 26px; list-style: none; }
  .social li { width: 20px; height: 20px; border-radius: 50%; background: #9b9b9b; }
</style>
</head>
<body>

<header class="site-header">
  <div class="brand">VELMO</div>
  <ul class="main-nav">
    <li class="active">Home</li>
    <li>Diary</li>
    <li>Theme Parties</li>
    <li>TV/TG and Admirers</li>
    <li>Membership</li>
    <li>FAQs</li>
    <li>Rooms</li>
    <li>Contact Us</li>
    <li>Links</li>
  </ul>
</header>

<section class="hero">
  <div class="hero-photo" role="img" aria-label="Warmly lit club lounge with brick walls, sofas and zebra-print seats"></div>
  <div class="hero-text">
    <div class="hero-title">WELCOME TO VELMO</div>
    <div class="hero-sub">We are a Swingers Club in the UK.</div>
    <div class="hero-lead">Velmo is one of the countries leading clubs and emphasises<br>friendliness, fun &amp; safety for its members.</div>
  </div>
  <div class="hero-dots"><i class="on"></i><i></i><i></i><i></i></div>
</section>

<section class="intro">
  <h1><b>VELMO ::</b> A TRUE SWINGERS CLUB WHERE YOU CAN MEET,<br>SOCIALISE AND PLAY (IF YOU WANT.......)</h1>
  <p>We are the best Swingers Club in the North East, and also voted <em>No 2 club in the UK.</em></p>
  <p>We have retained the coveted title of <em>No 1 friendliest club in the UK</em> (in joint 1st place with our great friends "Night Harbour Social", London).<br>This prestigious award has been given to us by a panel of "mystery voters" (swingers, singles &amp; couples) working with the publication called<br><b>"Nights Out Guide"</b> a copy of which is available in reception.</p>
  <p>Please see our <em>Frequently Asked Questions</em> and <em>Membership</em> pages for more information about the club and its facilities.</p>
  <p>Velmo was established in Eastbrook in 2003 by Alan (now retired) and has been at this location in Harlow Vale and run by Maria since 2009.<br>During this time we have upgraded and improved the club beyond recognition.</p>
</section>
<div class="btn-more">READ MORE</div>
<div class="divider"></div>

<section class="info dress">
  <div class="info-head">
    <svg width="58" height="48" viewBox="0 0 58 48" aria-hidden="true">
      <path d="M18 10 L6 16 L2 28 L12 30 L12 46 L46 46 L46 30 L56 28 L52 16 L40 10 Q29 18 18 10Z" fill="#ec1f27"/>
      <path d="M20 2 Q23 -1 24 3 M28 1 Q31 -2 32 2 M36 2 Q39 -1 40 3" stroke="#ec1f27" stroke-width="2" fill="none"/>
    </svg>
    <h2>DRESS</h2>
  </div>
  <p>Smart casual, no hoodies and caps please!</p>
  <p>Saturdays is a smart night out and people dress to impress.</p>
  <p>Wear what you would wear on a night out and bring lingerie, basques,<br>rubber etc to change into if you feel you want to dress down a bit.</p>
  <p><em>Guys</em> - dress to impress, remember ripped jeans on a Saturday night<br>just don't look the part.</p>
  <p><em>Ladies</em> - sexy or demure - whatever you wear, you will always<br>look lovely.</p>
</section>

<section class="info alcohol">
  <div class="info-head">
    <svg width="52" height="54" viewBox="0 0 52 54" aria-hidden="true">
      <rect x="7" y="2" width="8" height="10" fill="#ec1f27"/>
      <path d="M4 16 Q11 10 18 16 L18 52 L4 52Z" fill="none" stroke="#ec1f27" stroke-width="3"/>
      <path d="M26 22 L48 22 Q48 36 37 38 Q26 36 26 22Z" fill="none" stroke="#ec1f27" stroke-width="3"/>
      <path d="M37 38 L37 50 M30 51 L44 51" stroke="#ec1f27" stroke-width="3"/>
    </svg>
    <h2>ALCOHOL</h2>
  </div>
  <p>Please bring your own alcoholic drinks, which we will put behind the<br>bar (chilled as necessary) and serve to you.</p>
  <p>We do charge a corkage charge to help towards our bar staff costs,<br>glasses, ice, lemons &amp; limes etc, this charge is a nominal £1 charge per<br>person, per evening (NOT per bottle or can).</p>
  <p>We ask that you buy your soft drinks/tea/coffee etc from us.</p>
</section>

<section class="blog">
  <h2 class="section-title">Blog Posts</h2>
  <div class="blog-list">
    <article class="post">
      <div class="post-photo" role="img" aria-label="Bedroom with twin beds and patterned wallpaper" style="background: linear-gradient(160deg,#6a3a30,#c9b8a8 60%,#8a6a55);"></div>
      <h3>Vestibulum ante ipsum primis in<br>faucibus orci luctus..</h3>
      <time>JUN 18, 2017</time>
    </article>
    <article class="post">
      <div class="post-photo" role="img" aria-label="Bedroom with a double bed and lamps" style="background: linear-gradient(170deg,#4a4548,#d8d2cc 60%,#6b5a4c);"></div>
      <h3>Vestibulum ante ipsum primis in<br>faucibus orci luctus..</h3>
      <time>JUN 18, 2017</time>
    </article>
    <article class="post">
      <div class="post-photo" role="img" aria-label="Red-walled play room with furniture" style="background: linear-gradient(170deg,#8a1e14,#3a0d08 60%,#1a0805);"></div>
      <h3>Vestibulum ante ipsum primis in<br>faucibus orci luctus..</h3>
      <time>JUN 18, 2017</time>
    </article>
  </div>
</section>

<section class="shop">
  <h2 class="section-title">Velmo Merchandise For Sale</h2>
  <div class="products">
    <div class="product">
      <div class="product-photo" role="img" aria-label="Black drawstring bag with club name" style="background: linear-gradient(#3a3a3a,#111);"></div>
      <h4>Product Heading</h4>
      <p>Lorem ipsum dolor sit amet</p>
      <div class="product-buy"><span class="price">$10.00</span><span class="store">tradeva</span></div>
    </div>
    <div class="product">
      <div class="product-photo" role="img" aria-label="Black T-shirt with club name" style="background: linear-gradient(#2e2e2e,#0d0d0d);"></div>
      <h4>Product Heading</h4>
      <p>Lorem ipsum dolor sit amet</p>
      <div class="product-buy"><span class="price">$10.00</span><span class="store">tradeva</span></div>
    </div>
    <div class="product">
      <div class="product-photo" role="img" aria-label="Red cap with club name" style="background: linear-gradient(#e8343a,#a8141a);"></div>
      <h4>Product Heading</h4>
      <p>Lorem ipsum dolor sit amet</p>
      <div class="product-buy"><span class="price">$10.00</span><span class="store">tradeva</span></div>
    </div>
    <div class="product">
      <div class="product-photo" role="img" aria-label="Black mug with club name" style="background: linear-gradient(#2a2a2a,#050505);"></div>
      <h4>Product Heading</h4>
      <p>Lorem ipsum dolor sit amet</p>
      <div class="product-buy"><span class="price">$10.00</span><span class="store">tradeva</span></div>
    </div>
  </div>
</section>

<footer class="site-footer">
  <div class="footer-brand">VELMO</div>
  <div class="copyright">Copyright © 2010-2017 Velmo<br>All Right Reserved</div>

  <div class="footer-col sitemap">
    <h5>Site Map</h5>
    <ul style="left:0">
      <li>Home</li><li>Diary</li><li>Theme Parties</li><li>TV/TG and Admirers</li><li>Membership</li>
    </ul>
    <ul style="left:170px">
      <li>FAQs</li><li>Rooms</li><li>Contact US</li><li>Links</li>
    </ul>
  </div>

  <div class="footer-col newsletter">
    <h5>Newsletter Sign Up</h5>
    <p>Vestibulum ante ipsum primis in f<br>aucibus orci luctus.</p>
    <div class="signup">
      <span>Enter Email Address</span>
      <b><svg width="14" height="16" viewBox="0 0 14 16" aria-hidden="true"><path d="M3 2 L10 8 L3 14" stroke="#fbfbfb" stroke-width="3" fill="none"/></svg></b>
    </div>
  </div>

  <div class="footer-col follow">
    <h5>Follow Us</h5>
    <ul class="social" aria-label="Social links">
      <li></li><li></li><li></li><li></li><li></li><li></li>
    </ul>
  </div>
</footer>

</body>
</html>
```